Business card for my new company (Accounting firm)

I need a business card for my new business Brightwell Advisory and Ledger SA. Our services are accounting, tax, audit and financial management. Our customers are small companies, start-ups and new companies. The final design has to show financial security, trust and growth. Please find our logo attached to the business card. Text for the business card: Brightwell Advisory and Ledger SA Tomas Varenholt Director and Founder Certified Accountant Tel. 022 418 57 34 tv@clairevalconseil.ch www.clairevalconseil.ch Rue des Vergières 27 1201 Geneva
Target Market(s)
Our customers are small companies, start-ups and new companies.
Industry/Entity Type
Finance And Accounting
Contact Information for Business Card
Claireval Conseil et Comptes SA
Tomas Varenholt
Directeur et Fondateur
Expert-comptable diplômé
Tél. 022 418 57 34
tv@clairevalconseil.ch
www.clairevalconseil.ch
Rue des Vergières 27
1201 Genève

```html
<!DOCTYPE html>
<html lang="en">
<head>
<meta charset="utf-8">
<title>Claireval Conseil et Comptes SA – Business Card</title>
<link rel="stylesheet" href="https://fonts.googleapis.com/css2?family=Lato:wght@400;700&display=swap">
<style>
  :root {
    --page-bg: #e6e7e9;
    --card-light: #ffffff;
    --card-light-edge: #f0f1f2;
    --panel-dark: #3d3e40;
    --accent-blue: #29a3de;
    --text-light: #f2f2f2;
    --text-muted: #d4d5d6;
    --brand-ink: #3d3e40;
  }
  * { box-sizing: border-box; margin: 0; padding: 0; }
  html, body {
    width: 1200px; height: 900px; overflow: hidden;
    background: var(--page-bg);
  }
  .business-card {
    position: absolute; left: 100px; top: 140px;
    width: 1000px; height: 620px;
    background: linear-gradient(135deg, var(--card-light) 40%, var(--card-light-edge) 100%);
    box-shadow: 0 12px 40px rgba(0,0,0,0.18);
    overflow: hidden;
    font-family: 'Lato', sans-serif;
  }
  .card-shapes { position: absolute; inset: 0; }
  .contact-side { position: absolute; left: 49px; top: 86px; color: var(--text-light); }
  .holder-name {
    font-weight: 700; font-size: 31px; color: var(--accent-blue);
    letter-spacing: 0.3px; line-height: 40px;
  }
  .holder-role { font-size: 26px; line-height: 36px; }
  .contact-list { list-style: none; margin-top: 38px; }
  .contact-list li {
    display: flex; align-items: center; gap: 12px;
    font-size: 26px; line-height: 37px;
  }
  .contact-icon { width: 20px; height: 20px; flex: none; }
  .office-address {
    margin-top: 36px; font-size: 26px; line-height: 37px;
    color: var(--text-muted); font-style: normal;
  }
  .brand-block {
    position: absolute; left: 560px; top: 262px; width: 380px;
    display: flex; align-items: center; gap: 20px;
  }
  .brand-mark {
    width: 56px; height: 56px; flex: none;
    background: var(--accent-blue); border-radius: 50%;
  }
  .brand-name {
    font-family: 'Lato', sans-serif; font-weight: 400;
    font-size: 34px; line-height: 42px; color: var(--brand-ink);
  }
</style>
</head>
<body>
  <article class="business-card">
    <svg class="card-shapes" width="1000" height="620" viewBox="0 0 1000 620" aria-hidden="true">
      <polygon points="0,0 652,0 297,620 0,620" fill="var(--panel-dark)"/>
      <polygon points="652,0 662,0 307,620 297,620" fill="var(--accent-blue)"/>
    </svg>

    <section class="contact-side">
      <h1 class="holder-name">TOMAS VARENHOLT</h1>
      <p class="holder-role">Director and Founder</p>
      <p class="holder-role">Certified Accountant</p>

      <ul class="contact-list">
        <li>
          <svg class="contact-icon" viewBox="0 0 20 20" aria-hidden="true">
            <path d="M2 6c0-2 3-3 8-3s8 1 8 3v2h-4V6.5C13 6 7 6 6 6.5V8H2z" fill="var(--accent-blue)"/>
            <path d="M5 9h10l2 8H3z" fill="var(--accent-blue)"/>
            <circle cx="10" cy="13" r="2" fill="var(--panel-dark)"/>
          </svg>
          <span>022 418 57 34</span>
        </li>
        <li>
          <svg class="contact-icon" viewBox="0 0 20 20" aria-hidden="true">
            <rect x="1" y="4" width="18" height="12" fill="var(--accent-blue)"/>
            <path d="M1.5 4.5 10 11l8.5-6.5" fill="none" stroke="var(--panel-dark)" stroke-width="1.6"/>
          </svg>
          <span>tv@clairevalconseil.ch</span>
        </li>
        <li>
          <svg class="contact-icon" viewBox="0 0 20 20" aria-hidden="true">
            <circle cx="10" cy="10" r="8.5" fill="var(--accent-blue)"/>
            <path d="M6 5c2 1 2 3 4 3s1 3-1 4-1 3-2 4M13 4c-1 2 1 3 3 3M12 13c1 1 2 1 3 0" fill="none" stroke="var(--panel-dark)" stroke-width="1.4"/>
          </svg>
          <span>www.clairevalconseil.ch</span>
        </li>
      </ul>

      <address class="office-address">
        Rue des Vergières 27<br>1201 Geneva
      </address>
    </section>

    <div class="brand-block">
      <span class="brand-mark" aria-hidden="true"></span>
      <p class="brand-name">Claireval Conseil<br>et Comptes SA</p>
    </div>
  </article>
</body>
</html>
```